3D abstract logo Construction, Kitchen and Bath design and Project Management Business Card Design

I want a 3d abstract logo for a new General Construction, Kitchen and Bath design and Project Management Company located at Philadelphia PA, we want to put our logo in the white color trucks too. I want to look professional and serious at the same time look like an architect design and the warm originals color that make you feel in a nice decorated home, I like the colors trend in this link:
http://www.quellmark.example/qm/ggs/pageeditor.aspx?alt_doc_id=RT41K-M9B33-2W5&doc_id=5913046628&pf_id=D4H

I was thinking about a roof and the PA font could have square shape or like wood framing with two tones of the brick color black and creamy yellow color.... Also I like the keystone Idea like the modification or the Ridgeline Parkway logo but curvy at the top

The final design should communicate big company (because we want to grow), responsible, professional and organized that really care about our customers and give them everything they need... plan and design, excellent labor and Project Management
Updates

I doesn't have to be 3d

Reason: I haven't received enough options...

Please stick with the warm tones shown in the image001 attached I like spicy cinnamon instead a cold wine or brick color and also the cream yellowish tones added

Hello designers, please use only the idea and colors of the image001 I don't want to be stick with a house logo because I do commercial construction too so I prefer work around the keystone idea maybe leaving the style of the PA.
I'd like the base tone on the card dark like first option and you can send me a white option too.

Please send me your ideas as soon as possible 

Thank you so much!

Target Market(s)

Builders, State, commercial business owners, Property owners or Real State and Property Management Companies

Industry/Entity Type

Architect

Contact Information for Business Card

RK Buildworks LLC
“Your project is our business”
Lorna Vasquel Eng.
President
Commercial & Residential General Construction
Kitchen & Bath Design | Project Management
Phone: 555-304-7718 | Fax: 555-304-7719 Cell: 555-862-3097
lorna@rkbuildworks.example

```html
<!DOCTYPE html>
<html lang="en">
<head>
<meta charset="utf-8">
<title>RK Buildworks – Business Cards</title>
<link rel="stylesheet" href="https://fonts.googleapis.com/css2?family=Arimo:ital,wght@0,400;0,700;1,400&display=swap">
<style>
  :root {
    --cinnamon: #7a1f1c;
    --tan: #b29c82;
    --tan-light: #cbb9a3;
    --cream: #efe6d8;
    --paper: #ffffff;
    --ink: #1e1b18;
    --label: #8d8780;
    --backdrop: #e9e5df;
  }
  * { box-sizing: border-box; margin: 0; padding: 0; }
  html, body {
    width: 1200px; height: 870px; overflow: hidden;
    background: var(--backdrop);
    font-family: "Arimo", Arial, sans-serif;
  }
  .canvas { position: relative; width: 1200px; height: 870px; }

  .card {
    position: absolute;
    box-shadow: 0 6px 18px rgba(0,0,0,.18);
    overflow: hidden;
  }

  /* Back of card */
  .card-back {
    left: 120px; top: 130px; width: 340px; height: 600px;
    background: var(--tan);
    text-align: center;
  }
  .brand-disc {
    position: absolute; left: 50%; top: 160px;
    width: 206px; height: 196px; margin-left: -103px;
    border-radius: 50%;
    background: var(--cinnamon);
    display: flex; align-items: center; justify-content: center;
  }
  .brand-name {
    color: var(--paper);
    font-size: 26px; font-weight: 400; line-height: 1.15;
  }
  .tagline {
    position: absolute; left: 0; right: 0; top: 374px;
    color: var(--cinnamon); font-size: 21px;
  }
  .website {
    position: absolute; left: 0; right: 0; top: 538px;
    color: var(--cream); font-size: 15px; letter-spacing: .3px;
  }

  /* Front of card */
  .card-front {
    left: 555px; top: 270px; width: 590px; height: 340px;
    background: var(--paper);
  }
  .front-swoosh { position: absolute; inset: 0; }
  .person { position: absolute; left: 38px; top: 34px; }
  .person-name {
    color: var(--cinnamon); font-weight: 700; font-size: 38px; letter-spacing: .5px;
  }
  .person-title {
    color: var(--cinnamon); font-style: italic; font-size: 21px; margin-top: 2px;
  }
  .services {
    position: absolute; left: 38px; top: 118px; width: 440px;
    color: var(--tan-light); font-size: 19px; line-height: 1.2;
  }
  .contacts {
    position: absolute; left: 38px; top: 222px;
    display: grid; grid-template-columns: 82px auto; row-gap: 5px;
    font-size: 15px;
  }
  .contacts dt { color: var(--label); }
  .contacts dd { color: var(--ink); }
  .front-mark {
    position: absolute; left: 466px; top: 228px;
    width: 104px; height: 100px; border-radius: 50%;
    background: var(--cinnamon);
    display: flex; align-items: center; justify-content: center;
  }
  .front-mark .brand-name { font-size: 14px; }
</style>
</head>
<body>
<main class="canvas">

  <section class="card card-back" aria-label="Card back">
    <div class="brand-disc"><span class="brand-name">RK<br>Buildworks</span></div>
    <p class="tagline">Your project is our business</p>
    <p class="website">www.rkbuildworks.example</p>
  </section>

  <section class="card card-front" aria-label="Card front">
    <svg class="front-swoosh" viewBox="0 0 590 340" preserveAspectRatio="none" aria-hidden="true">
      <path d="M590 55 C520 95 470 210 372 340 L590 340 Z" fill="var(--tan)"/>
      <path d="M590 42 C510 88 458 205 356 340" fill="none" stroke="var(--cinnamon)" stroke-width="2"/>
      <path d="M590 30 C500 80 446 200 340 340" fill="none" stroke="var(--tan-light)" stroke-width="1.5"/>
    </svg>

    <div class="person">
      <h1 class="person-name">LORNA VASQUEL</h1>
      <p class="person-title">Eng. President</p>
    </div>

    <p class="services">Commercial &amp; Residential General Con-<br>struction Kitchen &amp; Bath Design</p>

    <dl class="contacts">
      <dt>Phone:</dt><dd>555-304-7718</dd>
      <dt>Fax:</dt><dd>555-304-7719</dd>
      <dt>Cell:</dt><dd>555-862-3097</dd>
      <dt>Email:</dt><dd>lorna@rkbuildworks.example</dd>
    </dl>

    <div class="front-mark"><span class="brand-name">RK<br>Buildworks</span></div>
  </section>

</main>
</body>
</html>
```